UI Improvement for FlorKeep app

We are looking for a talented UI/UX designer to REFINE and enhance the visual design of our mobile application, FlorKeep. The app is fully functional, but we need a designer to improve its aesthetics by specifying design elements such as fonts, colors, spacing, and component styles.
Your task will be to analyze the CURRENT UI and provide detailed design specifications that will make the app more visually appealing, modern, and user-friendly.
TODO:
Review the existing FlorKeep app design (see attachments) and identify areas for visual improvement.
Provide a detailed UI style guide, including:
Typography (font choices, sizes, and weights)
Color palette (primary, secondary, and accent colors)
Component styling (buttons, forms, icons, and interactive elements)
Spacing and layout guidelines (margins, paddings, and alignment)
Ensure the design remains clean, modern, and professional while maintaining usability and accessibility.
Provide design mockups or visual examples (if possible) to illustrate the proposed changes.
Deliverables:
A UI Style Guide (PDF or Figma file) with specifications on fonts, colors, spacing, and UI components.
Optionally, before/after mockups or examples demonstrating the improvements.
Ideal Designer:
Strong experience in mobile UI/UX design.
Understanding of modern design trends and best practices.
Ability to communicate design choices clearly for easy developer implementation.
I have attached 7 images showcasing the main UI screens used in the FlorKeep app. These screens need visual enhancements to improve their overall look and user experience.
The images represent the current design in three key modes:
LIST Mode – Displays data in a structured list format.
READ Mode – Shows detailed information when a user selects an item.
ADD/EDIT Mode – Allows users to input or modify information.
Additionally, there is a ‘MORE’ page, which serves as a menu listing other features of the application.
Task Objective:
Please refine and improve these UIs to create a more modern, visually appealing, and user-friendly experience. Focus on typography, colors, spacing, and component styling to ensure a cohesive and polished design.
Look and feel
Each slider illustrates characteristics of the customer's brand and the style your logo design should communicate.

```html
<!DOCTYPE html>
<html lang="en">
<head>
<meta charset="utf-8">
<title>FlorKeep – WorkOrder</title>
<link rel="stylesheet" href="https://fonts.googleapis.com/css2?family=Poppins:wght@400;500;600;700&display=swap">
<style>
:root{
  --blue:#2d8bd0;
  --blue-dark:#1f6fae;
  --ink:#2b2f38;
  --muted:#6b7280;
  --page:#dfe6ef;
  --surface:#ffffff;
  --line:#e4e8ee;
  --tab-active:#2d8bd0;
}
*{box-sizing:border-box;margin:0;padding:0}
html,body{width:758px;height:1200px;overflow:hidden}
body{font-family:"Poppins",sans-serif;color:var(--ink);background:var(--page);position:relative}
.status-bar{height:70px;background:var(--surface);display:flex;align-items:center;justify-content:space-between;padding:0 44px;font-weight:600;font-size:26px}
.status-icons{display:flex;gap:12px;align-items:center}
.app-header{height:100px;background:var(--surface);display:flex;align-items:center;justify-content:space-between;padding:0 34px;border-bottom:1px solid var(--line)}
.app-title{font-size:52px;font-weight:600;letter-spacing:-.5px}
.content{padding:22px 28px}
.mode-tabs{display:flex;justify-content:space-between;align-items:center;background:var(--surface);border-radius:12px;padding:10px 12px;font-size:25px;font-weight:500}
.mode-tab{padding:8px 12px;border-radius:6px}
.mode-tab.is-active{background:var(--tab-active);color:#fff}
.customer-card{margin-top:22px;background:var(--surface);border-radius:22px;padding:28px 30px 36px;box-shadow:0 4px 12px rgba(40,60,90,.08)}
.customer-head{display:flex;align-items:center;gap:20px;position:relative}
.customer-name{font-size:32px;font-weight:600;line-height:1.2}
.customer-role{font-size:22px;color:var(--blue)}
.card-menu{position:absolute;right:0;top:10px}
.detail-grid{display:grid;grid-template-columns:1fr 1fr;gap:28px 30px;margin-top:30px;padding-left:20px}
.detail-label{font-size:26px;font-weight:600;color:var(--blue);line-height:1.3}
.detail-value{font-size:20px;color:var(--ink);line-height:1.4;margin-top:4px}
.add-row{margin-top:22px;background:var(--surface);border-radius:14px;height:78px;display:flex;align-items:center;justify-content:space-between;padding:0 26px;font-size:23px;font-weight:600}
.bottom-nav{position:absolute;left:0;right:0;bottom:0;height:112px;background:var(--surface);display:flex;justify-content:space-around;align-items:center;border-top:1px solid var(--line)}
.nav-item{display:flex;flex-direction:column;align-items:center;gap:6px;font-size:19px;font-weight:600;color:var(--ink)}
.nav-item.is-active{color:var(--blue)}
</style>
</head>
<body>
<div class="status-bar">
  <span>9:45</span>
  <span class="status-icons">
    <svg width="30" height="20" viewBox="0 0 30 20"><rect x="0" y="14" width="5" height="6" fill="#2b2f38"/><rect x="8" y="10" width="5" height="10" fill="#2b2f38"/><rect x="16" y="5" width="5" height="15" fill="#2b2f38"/><rect x="24" y="0" width="5" height="20" fill="#2b2f38"/></svg>
    <svg width="28" height="20" viewBox="0 0 28 20"><path d="M2 7a17 17 0 0 1 24 0M6 11a11 11 0 0 1 16 0M10 15a5 5 0 0 1 8 0" stroke="#2b2f38" stroke-width="3" fill="none" stroke-linecap="round"/></svg>
    <svg width="42" height="20" viewBox="0 0 42 20"><rect x="1" y="1" width="36" height="18" rx="4" fill="none" stroke="#2b2f38" stroke-width="2"/><rect x="4" y="4" width="30" height="12" rx="2" fill="#2b2f38"/><rect x="38" y="7" width="3" height="6" rx="1" fill="#2b2f38"/></svg>
  </span>
</div>

<header class="app-header">
  <svg width="40" height="40" viewBox="0 0 40 40"><path d="M26 6 12 20l14 14" stroke="#6b7280" stroke-width="3.5" fill="none" stroke-linecap="round" stroke-linejoin="round"/></svg>
  <h1 class="app-title">WorkOrder</h1>
  <svg width="40" height="40" viewBox="0 0 40 40"><circle cx="20" cy="8" r="3.5" fill="#6b7280"/><circle cx="20" cy="20" r="3.5" fill="#6b7280"/><circle cx="20" cy="32" r="3.5" fill="#6b7280"/></svg>
</header>

<main class="content">
  <nav class="mode-tabs">
    <span class="mode-tab">Print</span>
    <span class="mode-tab">Create</span>
    <span class="mode-tab">Extra Soft</span>
    <span class="mode-tab">Soft</span>
    <span class="mode-tab is-active">Medium</span>
    <span class="mode-tab">Hard</span>
  </nav>

  <section class="customer-card">
    <div class="customer-head">
      <svg width="78" height="78" viewBox="0 0 78 78"><circle cx="39" cy="39" r="39" fill="#2d8bd0"/><circle cx="39" cy="30" r="12" fill="#fff"/><path d="M17 62a22 18 0 0 1 44 0z" fill="#fff"/></svg>
      <div>
        <div class="customer-name">Marsh, Elena</div>
        <div class="customer-role">Customer →</div>
      </div>
      <svg class="card-menu" width="40" height="12" viewBox="0 0 40 12"><circle cx="6" cy="6" r="4" fill="#9aa3ae"/><circle cx="20" cy="6" r="4" fill="#9aa3ae"/><circle cx="34" cy="6" r="4" fill="#9aa3ae"/></svg>
    </div>
    <div class="detail-grid">
      <div><div class="detail-label">Service Location -e</div><div class="detail-value">Billing, 418 Larkfield Way, Dayton OH, 45402</div></div>
      <div><div class="detail-label">Billing Address -e</div><div class="detail-value">Billing, 418 Larkfield Way, Dayton OH, 45402</div></div>
      <div><div class="detail-label">Description -e</div><div class="detail-value">Pool maintenance</div></div>
      <div><div class="detail-label">Work Order Type -e</div><div class="detail-value">One off job -e</div></div>
      <div><div class="detail-label">WO Status -e</div><div class="detail-value">Active -e</div></div>
      <div><div class="detail-label">Billing Frequency -e</div><div class="detail-value">Upon job completion -e</div></div>
    </div>
  </section>

  <div class="add-row">
    <span>Add Technician -e</span>
    <svg width="32" height="32" viewBox="0 0 32 32"><rect x="2" y="2" width="28" height="28" rx="5" fill="none" stroke="#2d8bd0" stroke-width="2.5"/><path d="M16 9v14M9 16h14" stroke="#2d8bd0" stroke-width="2.5" stroke-linecap="round"/></svg>
  </div>
  <div class="add-row">
    <span>Add Line Items -e</span>
    <svg width="32" height="32" viewBox="0 0 32 32"><rect x="2" y="2" width="28" height="28" rx="5" fill="none" stroke="#2d8bd0" stroke-width="2.5"/><path d="M16 9v14M9 16h14" stroke="#2d8bd0" stroke-width="2.5" stroke-linecap="round"/></svg>
  </div>
</main>

<nav class="bottom-nav">
  <div class="nav-item">
    <svg width="34" height="34" viewBox="0 0 34 34"><circle cx="17" cy="11" r="7" fill="#2b2f38"/><path d="M4 32a13 11 0 0 1 26 0z" fill="#2b2f38"/></svg>
    <span>Contact</span>
  </div>
  <div class="nav-item">
    <svg width="34" height="34" viewBox="0 0 34 34"><path d="M4 8h10v10l-5 10H5l4-10H4zM19 8h10v10l-5 10h-4l4-10h-5z" fill="#2b2f38"/></svg>
    <span>Quote</span>
  </div>
  <div class="nav-item is-active">
    <svg width="34" height="34" viewBox="0 0 34 34"><rect x="3" y="10" width="28" height="20" rx="4" fill="#2d8bd0"/><path d="M12 10V6h10v4" stroke="#2d8bd0" stroke-width="3" fill="none"/><rect x="3" y="17" width="28" height="2" fill="#fff"/></svg>
    <span>WorkOrder</span>
  </div>
  <div class="nav-item">
    <svg width="34" height="34" viewBox="0 0 34 34"><rect x="7" y="3" width="22" height="28" rx="3" fill="#2b2f38"/><path d="M12 11h12M12 16h12M12 21h8" stroke="#fff" stroke-width="2"/></svg>
    <span>Invoice</span>
  </div>
  <div class="nav-item">
    <svg width="34" height="34" viewBox="0 0 34 34"><circle cx="6" cy="17" r="3.5" fill="#2b2f38"/><circle cx="17" cy="17" r="3.5" fill="#2b2f38"/><circle cx="28" cy="17" r="3.5" fill="#2b2f38"/></svg>
    <span>More</span>
  </div>
</nav>
</body>
</html>
```